Commercial Real Estate Property Sign

Design a 4' x 4' sign that pops. Refer to examples.

Must include the following information:
A space to list (For Sale, For Lease, Build-to-Suite or Available)
BrightKeel,LLC
Commercial Real Estate
company website
My Name (Marcus Pellow)
My Phone #

Industry/Entity Type

Real Estate

```html
<!DOCTYPE html>
<html lang="en">
<head>
<meta charset="utf-8">
<title>BrightKeel LLC – Space for Lease Sign</title>
<link href="https://fonts.googleapis.com/css2?family=Barlow:wght@400;500;700;800&display=swap" rel="stylesheet">
<style>
  :root {
    --charcoal: #3a3a3a;
    --orange: #e8650a;
    --white: #ffffff;
    --ink: #1c1c1c;
    --font: "Barlow", sans-serif;
  }
  * { margin: 0; padding: 0; box-sizing: border-box; }
  html, body { width: 1200px; height: 1200px; overflow: hidden; background: var(--white); }
  .sign {
    position: relative;
    width: 1200px;
    height: 1200px;
    font-family: var(--font);
    display: grid;
    grid-template-rows: 274px 540px 200px 186px;
  }
  .band { display: flex; flex-direction: column; align-items: center; justify-content: center; }
  .band--brand { background: var(--charcoal); }
  .band--contact { background: var(--orange); gap: 6px; }
  .band--listing { background: var(--charcoal); }
  .band--web { background: var(--orange); }

  .brand-row { display: flex; align-items: center; gap: 26px; margin-top: 10px; }
  .brand-mark { width: 34px; height: 34px; background: var(--orange); }
  .brand-name {
    color: var(--white);
    font-size: 96px;
    font-weight: 500;
    letter-spacing: 14px;
    line-height: 1;
  }
  .tagline {
    display: flex; align-items: center; gap: 14px;
    width: 100%;
    margin-top: 14px;
    color: var(--white);
    font-size: 43px;
    font-weight: 400;
    letter-spacing: 1px;
  }
  .tagline::before, .tagline::after {
    content: ""; flex: 1; height: 3px; background: var(--orange);
  }

  .agent-name { color: var(--ink); font-size: 84px; font-weight: 400; line-height: 1.1; letter-spacing: 1px; }
  .agent-phone { color: var(--ink); font-size: 112px; font-weight: 800; line-height: 1.1; letter-spacing: 3px; }

  .listing-status { color: var(--white); font-size: 110px; font-weight: 800; line-height: 1; }
  .listing-status .accent { color: var(--orange); }

  .website { display: flex; align-items: center; gap: 18px; color: var(--ink); font-size: 78px; font-weight: 700; letter-spacing: 1px; }
  .website-icon { width: 42px; height: 42px; }
</style>
</head>
<body>
  <main class="sign">
    <header class="band band--brand">
      <div class="brand-row">
        <span class="brand-mark"></span>
        <span class="brand-name">BrightKeel LLC</span>
      </div>
      <div class="tagline">Commercial Real Estate</div>
    </header>

    <section class="band band--contact">
      <p class="agent-name">Marcus Pellow</p>
      <p class="agent-phone">469.555.0182</p>
    </section>

    <section class="band band--listing">
      <p class="listing-status"><span class="accent">F</span>or Space for <span class="accent">L</span>ease</p>
    </section>

    <footer class="band band--web">
      <p class="website">
        <svg class="website-icon" viewBox="0 0 42 42" fill="none" stroke="#1c1c1c" stroke-width="3">
          <circle cx="21" cy="21" r="18"/>
          <ellipse cx="21" cy="21" rx="8" ry="18"/>
          <line x1="3" y1="21" x2="39" y2="21"/>
          <path d="M6 12h30M6 30h30"/>
        </svg>
        www.mybrightkeel.com
      </p>
    </footer>
  </main>
</body>
</html>
```